BOLD & MINIMALIST DESIGN NEEDED

We want a very bold but minimalistic business card design that is impactful and utilizes both sides of the business card. Our current logo is included for your use.

We want bold fonts and good use of negative space. We don't want the logo to overpower the design.

Target Market(s)

Professionals who are building new commercial buildings.

Industry/Entity Type

Construction

Contact Information for Business Card

Name, Title, email, office phone, cell phone, website

Font styles to use
Serif
Sans Serif

Requirements
Must have
• Bold design!

```html
<!DOCTYPE html>
<html lang="en">
<head>
<meta charset="utf-8">
<title>Summitline Design + Build — Business Card</title>
<link rel="stylesheet" href="https://fonts.googleapis.com/css2?family=Montserrat:wght@500;800&family=Poppins:wght@400&display=swap">
<style>
  :root {
    --bg: #2b2b2b;
    --green: #84c128;
    --white: #ffffff;
    --ink: #111111;
  }
  * { margin: 0; padding: 0; box-sizing: border-box; }
  html, body { width: 1200px; height: 1015px; overflow: hidden; background: var(--bg); }
  .canvas {
    width: 1200px; height: 1015px;
    display: flex; flex-direction: column; align-items: center; justify-content: center; gap: 56px;
  }
  .card {
    position: relative; width: 760px; height: 434px;
    background: var(--white); overflow: hidden;
    box-shadow: 0 14px 36px rgba(0,0,0,.55);
  }
  .card__band { position: absolute; inset: 0; width: 100%; height: 100%; }
  .brand {
    position: absolute; display: flex; align-items: center; gap: 14px;
    font-family: "Montserrat", sans-serif; font-weight: 800; color: var(--ink);
    text-transform: uppercase; line-height: 1.05;
  }
  .brand__mark { width: 30px; height: 30px; flex: none; }
  .brand__name { font-size: 34px; letter-spacing: .5px; }
  .brand__name span { display: block; font-size: 15px; letter-spacing: 6px; }
  .front .brand { left: 200px; top: 150px; }
  .front .brand__mark { background: var(--ink); }
  .back .brand { left: 70px; top: 300px; }
  .back .brand__mark { background: var(--green); }
  .contact {
    position: absolute; right: 60px; top: 70px; width: 300px;
    font-family: "Poppins", sans-serif; color: var(--ink);
  }
  .contact__name {
    font-family: "Montserrat", sans-serif; font-weight: 800; font-size: 26px;
    text-transform: uppercase; letter-spacing: .3px;
    border-bottom: 1.5px solid var(--ink); padding-bottom: 2px;
  }
  .contact__title {
    font-family: "Montserrat", sans-serif; font-weight: 500; font-size: 13px;
    text-transform: uppercase; letter-spacing: .5px; margin-top: 4px;
  }
  .contact__list { list-style: none; margin-top: 26px; }
  .contact__item { display: flex; align-items: center; gap: 10px; font-size: 17px; line-height: 1.55; }
  .contact__icon { width: 16px; height: 16px; flex: none; }
</style>
</head>
<body>
<main class="canvas">

  <section class="card front" aria-label="Card front">
    <svg class="card__band" viewBox="0 0 760 434" preserveAspectRatio="none" aria-hidden="true">
      <polygon points="0,0 300,0 760,200 760,434 230,434 0,330" fill="var(--green)"/>
    </svg>
    <div class="brand">
      <div class="brand__mark"></div>
      <div class="brand__name">Summitline<span>Design + Build</span></div>
    </div>
  </section>

  <section class="card back" aria-label="Card back">
    <svg class="card__band" viewBox="0 0 760 434" preserveAspectRatio="none" aria-hidden="true">
      <polygon points="0,0 610,0 760,90 760,360 0,130" fill="var(--green)"/>
    </svg>
    <div class="contact">
      <div class="contact__name">Marcus Hale</div>
      <div class="contact__title">Managing Director</div>
      <ul class="contact__list">
        <li class="contact__item">
          <svg class="contact__icon" viewBox="0 0 16 16"><path d="M3 1.5l3 3-1.6 1.8a9 9 0 0 0 5.3 5.3L11.5 10l3 3-1.8 2C7 15 1 9 1 3.3z" fill="var(--ink)"/></svg>
          044-987 654 321
        </li>
        <li class="contact__item">
          <svg class="contact__icon" viewBox="0 0 16 16"><rect x="4" y="1" width="8" height="14" rx="1.5" fill="none" stroke="var(--ink)" stroke-width="1.6"/><circle cx="8" cy="12.5" r="0.9" fill="var(--ink)"/></svg>
          044-987 654 322
        </li>
        <li class="contact__item">
          <svg class="contact__icon" viewBox="0 0 16 16"><rect x="1" y="3" width="14" height="10" fill="var(--ink)"/><path d="M1 3l7 6 7-6" fill="none" stroke="var(--green)" stroke-width="1.3"/></svg>
          info@summitline.com
        </li>
        <li class="contact__item">
          <svg class="contact__icon" viewBox="0 0 16 16" fill="none" stroke="var(--ink)" stroke-width="1.3"><circle cx="8" cy="8" r="6.5"/><ellipse cx="8" cy="8" rx="3" ry="6.5"/><path d="M1.5 8h13M2.5 4.7h11M2.5 11.3h11"/></svg>
          www.summitline.com
        </li>
      </ul>
    </div>
    <div class="brand">
      <div class="brand__mark"></div>
      <div class="brand__name">Summitline<span>Design + Build</span></div>
    </div>
  </section>

</main>
</body>
</html>
```